SaaS Early tech startup business card design

Unique design for experience ecommerce platform company. the business cards will be used by executive members. conformance with color code is required.

```html
<!DOCTYPE html>
<html lang="en">
<head>
<meta charset="utf-8">
<title>novix business card</title>
<link href="https://fonts.googleapis.com/css2?family=Roboto:wght@400;500;700;900&display=swap" rel="stylesheet">
<style>
  :root {
    --brand-blue: #0b5b8e;
    --brand-teal: #19a88f;
    --brand-deep: #0c7f92;
    --ink: #3a3a3a;
    --card-white: #ffffff;
    --stage: #cfd0d2;
    --divider: #0b5b8e;
  }
  * { margin: 0; padding: 0; box-sizing: border-box; }
  html, body {
    width: 1200px; height: 800px; overflow: hidden;
    background: var(--stage);
    font-family: "Roboto", Arial, sans-serif;
  }
  .canvas {
    position: relative; width: 1200px; height: 800px;
    display: flex; align-items: center; justify-content: center; gap: 40px;
  }
  .card {
    position: relative; width: 540px; height: 309px;
    box-shadow: 0 10px 24px rgba(0,0,0,0.18);
    overflow: hidden;
  }
  /* Front */
  .card--front { background: var(--card-white); }
  .front__wordmark {
    position: absolute; top: 46px; left: 290px;
    font-weight: 900; font-size: 66px; letter-spacing: -1px;
    color: var(--brand-blue); line-height: 1;
  }
  .front__identity { position: absolute; left: 34px; top: 166px; }
  .identity__name {
    font-weight: 700; font-size: 21px; color: var(--brand-blue);
    letter-spacing: 0.3px; line-height: 1.1;
  }
  .identity__role {
    font-weight: 500; font-size: 13px; color: var(--brand-teal); margin-top: 2px;
  }
  .front__band {
    position: absolute; left: 34px; right: 34px; top: 214px; height: 6px;
    background: repeating-linear-gradient(90deg,
      var(--brand-teal) 0 18px, var(--brand-deep) 18px 26px,
      var(--brand-blue) 26px 34px, var(--brand-teal) 34px 46px);
  }
  .front__contacts {
    position: absolute; left: 34px; right: 34px; top: 234px;
    display: flex; align-items: flex-start;
    font-size: 12.5px; color: var(--ink);
  }
  .contact-group { display: flex; flex-direction: column; gap: 5px; }
  .contact-group--phones { width: 130px; }
  .contact-group--web { width: 150px; }
  .contact-line { display: flex; align-items: center; gap: 7px; white-space: nowrap; }
  .contact-line svg { width: 11px; height: 11px; flex: none; }
  .contact-divider {
    width: 1px; height: 30px; background: var(--divider);
    transform: rotate(28deg); margin: 2px 26px 0 0;
  }
  .contact-group--address { line-height: 1.35; }
  /* Back */
  .card--back { background: var(--brand-deep); }
  .back__field {
    position: absolute; inset: 0;
    background: linear-gradient(160deg, #14a08f 0%, #0c8893 45%, #0b6a96 100%);
  }
  .back__wordmark {
    position: absolute; right: 40px; bottom: 70px;
    font-weight: 900; font-size: 74px; letter-spacing: -1px;
    color: var(--card-white); line-height: 1;
  }
</style>
</head>
<body>
<main class="canvas">
  <section class="card card--front" aria-label="Card front">
    <div class="front__wordmark">novix</div>

    <div class="front__identity">
      <div class="identity__name">DANIEL REED</div>
      <div class="identity__role">President</div>
    </div>

    <div class="front__band"></div>

    <div class="front__contacts">
      <div class="contact-group contact-group--phones">
        <div class="contact-line">
          <svg viewBox="0 0 12 12"><path d="M2.5 1 4.5 1 5.3 3.6 4 4.6C4.7 6 6 7.3 7.4 8L8.4 6.7 11 7.5 11 9.5C11 10.3 10.3 11 9.5 11 5 11 1 7 1 2.5 1 1.7 1.7 1 2.5 1Z" fill="var(--brand-teal)"/></svg>
          <span>555-214-7730</span>
        </div>
        <div class="contact-line">
          <svg viewBox="0 0 12 12"><rect x="3" y="1" width="6" height="10" rx="1" fill="none" stroke="var(--brand-teal)" stroke-width="1.4"/></svg>
          <span>555-618-2049</span>
        </div>
      </div>
      <div class="contact-divider"></div>
      <div class="contact-group contact-group--web">
        <div class="contact-line">
          <svg viewBox="0 0 12 12"><rect x="1" y="2.5" width="10" height="7" fill="var(--brand-teal)"/><path d="M1 2.5 6 6.5 11 2.5" fill="none" stroke="#fff" stroke-width="1"/></svg>
          <span>hello@novix.com</span>
        </div>
        <div class="contact-line">
          <svg viewBox="0 0 12 12"><circle cx="6" cy="6" r="5" fill="var(--brand-teal)"/><path d="M1 6H11M6 1C4 3.5 4 8.5 6 11M6 1C8 3.5 8 8.5 6 11" fill="none" stroke="#fff" stroke-width="0.8"/></svg>
          <span>www.novix.com</span>
        </div>
      </div>
      <div class="contact-divider"></div>
      <div class="contact-group contact-group--address">
        <span>1420 Harbor View Road</span>
        <span>Portland, Oregon 97205</span>
      </div>
    </div>
  </section>

  <section class="card card--back" aria-label="Card back">
    <div class="back__field" role="img" aria-label="Teal to blue checkered brand pattern"></div>
    <div class="back__wordmark">novix</div>
  </section>
</main>
</body>
</html>
```